New Webpage for High Class Expert Witness Services Company

We are looking for a minimalist design for a webpage that just has our logo and an entry form offer to connect with one of our Liaisons.
The entry form should just ask for Name, Email, Contact Info and Description of Project.

Company Name is: The Marlowe Crest Advisory Services

Number of Pages Required

1 page

```html
<!DOCTYPE html>
<html lang="en">
<head>
<meta charset="utf-8">
<title>Marlowe Crest Advisory Services — Connect With Us</title>
<link rel="stylesheet" href="https://fonts.googleapis.com/css2?family=Cinzel:wght@400;700&family=Manrope:wght@400&family=Roboto:wght@400&display=swap">
<style>
  :root {
    --bg-deep: #141415;
    --bg-mid: #1c1c1d;
    --bg-edge: #2a2a2b;
    --text-main: #ffffff;
    --text-muted: #bdbdbd;
    --text-soft: #9a9a9a;
    --line: #8a8a8a;
    --line-faint: #3a3a3b;
    --field-bg: #111112;
    --button-light: #d9d9db;
    --button-dark: #a6a6a9;
    --button-text: #121212;
  }
  * { box-sizing: border-box; margin: 0; padding: 0; }
  html, body { width: 1200px; height: 742px; overflow: hidden; background: var(--bg-deep); }
  .page { position: relative; width: 1200px; height: 742px; overflow: hidden; color: var(--text-main); }
  .backdrop {
    position: absolute; inset: 0;
    background:
      radial-gradient(ellipse 60% 70% at 50% 45%, var(--bg-deep) 0%, var(--bg-mid) 55%, var(--bg-edge) 100%);
  }
  .brand {
    position: absolute; left: 114px; top: 44px;
    display: flex; align-items: center; gap: 14px;
    font-family: "Cinzel", serif; font-weight: 400;
    font-size: 26px; letter-spacing: 1px; line-height: 1.05; color: #d6d6d6;
  }
  .brand-mark { width: 40px; height: 40px; background: #d6d6d6; flex: none; }
  .hero { position: absolute; left: 114px; top: 218px; width: 500px; }
  .hero-eyebrow {
    font-family: "Cinzel", serif; font-size: 15.5px; letter-spacing: 1.6px;
    color: var(--text-muted); margin-left: 6px;
  }
  .hero-title {
    margin-top: 17px;
    font-family: "Cinzel", serif; font-weight: 400;
    font-size: 52px; line-height: 51px; letter-spacing: 1.5px; color: var(--text-main);
  }
  .hero-text {
    margin-top: 15px; width: 480px;
    font-family: "Manrope", sans-serif; font-size: 14px; line-height: 27px; color: var(--text-muted);
  }
  .contact-panel {
    position: absolute; left: 715px; top: 124px; width: 379px; height: 438px;
    border: 1px solid var(--line); background: rgba(14,14,15,0.55);
  }
  .contact-title {
    position: absolute; left: 46px; top: 34px;
    font-family: "Cinzel", serif; font-weight: 400; font-size: 24px; letter-spacing: 0.5px;
  }
  .field {
    position: absolute; left: 46px; width: 294px; height: 42px;
    border: 1px solid var(--line); background: var(--field-bg);
    font-family: "Roboto", sans-serif; font-size: 13px; color: var(--text-main);
    padding: 0 17px; display: flex; align-items: center;
  }
  .field-name { top: 85px; }
  .field-email { top: 143px; }
  .field-phone { top: 197px; }
  .field-description { top: 254px; height: 88px; align-items: flex-start; padding-top: 11px; }
  .submit-button {
    position: absolute; left: 46px; top: 355px; width: 297px; height: 44px;
    background: linear-gradient(110deg, var(--button-light) 0%, var(--button-light) 45%, var(--button-dark) 75%, var(--button-dark) 100%);
    border-radius: 2px; display: flex; align-items: center; justify-content: center;
    font-family: "Cinzel", serif; font-weight: 700; font-size: 15px; letter-spacing: 0.5px; color: var(--button-text);
  }
  .site-footer {
    position: absolute; left: 0; top: 680px; width: 1200px; height: 62px;
    border-top: 1px solid var(--line-faint);
    display: flex; align-items: center; justify-content: center;
    font-family: "Roboto", sans-serif; font-size: 12px; color: var(--text-soft);
  }
</style>
</head>
<body>
  <main class="page">
    <div class="backdrop" role="img" aria-label="Dark background with faint sweeping fine-line waves"></div>

    <header class="brand">
      <span class="brand-mark"></span>
      <span class="brand-name">Marlowe Crest<br>Advisory Services</span>
    </header>

    <section class="hero">
      <p class="hero-eyebrow">MARLOWE CREST ADVISORY SERVICES</p>
      <h1 class="hero-title">SEAMLESS<br>MEDICAL EXPERT<br>INTEGRATION</h1>
      <p class="hero-text">Lorem ipsum dolor sit amet, consectetur adipiscing elit, sed do eiusmod tempor incididunt ut labore et dolore magna aliqua.</p>
    </section>

    <section class="contact-panel">
      <h2 class="contact-title">CONNECT WITH US</h2>
      <div class="field field-name">Name*</div>
      <div class="field field-email">Email*</div>
      <div class="field field-phone">Phone number*</div>
      <div class="field field-description">Description of Project</div>
      <div class="submit-button">SUBMIT</div>
    </section>

    <footer class="site-footer">© 2026 Marlowe Crest Advisory Services. All Rights Reserved</footer>
  </main>
</body>
</html>
```